Business Card Design for a Software Startup

We'd like to have a business card design. We already have a logo. Basically what we need is a clean design with name, address, cellphone and phone numbers, e-mail and web site address (front) and a space on the back with our logo with the company name on the right side and some texts on the bottom.
We are a development and consulting company in Brazil with highly qualified team of professionals in Java, iOS and Android development and consulting.

Target Market(s)

CIO, IT managers of mid to big size companies

Industry/Entity Type

Business

```html
<!DOCTYPE html>
<html lang="en">
<head>
<meta charset="utf-8">
<title>Vantro Business Card</title>
<link rel="stylesheet" href="https://fonts.googleapis.com/css2?family=Montserrat:wght@700&family=Questrial&display=swap">
<style>
  :root {
    --bg: #e9e6e1;
    --card: #ffffff;
    --navy: #0d3466;
    --blue: #1a6fad;
    --sky: #3fb3e6;
    --ink: #3a3a3a;
    --divider: #d4d9de;
  }
  * { margin: 0; padding: 0; box-sizing: border-box; }
  html, body { width: 1200px; height: 720px; overflow: hidden; }
  body {
    background: var(--bg);
    display: flex;
    align-items: center;
    justify-content: center;
    gap: 40px;
    font-family: "Questrial", sans-serif;
  }
  .card {
    position: relative;
    width: 520px;
    height: 297px;
    background: var(--card);
    box-shadow: 0 6px 18px rgba(0,0,0,0.18);
    overflow: hidden;
  }

  /* Contact side */
  .rule {
    position: absolute;
    left: 0; right: 0;
    height: 2px;
    background: var(--sky);
  }
  .rule--top { top: 24px; }
  .rule--bottom { top: 86px; }
  .name-band {
    position: absolute;
    left: 0; right: 0;
    top: 32px;
    height: 48px;
    background: var(--navy);
    color: #fff;
    display: flex;
    align-items: center;
    justify-content: flex-end;
    padding-right: 150px;
  }
  .name-band .person { font-family: "Montserrat", sans-serif; font-weight: 700; font-size: 19px; }
  .name-band .title { font-family: "Questrial", sans-serif; font-size: 15px; margin-left: 6px; }
  .brand {
    position: absolute;
    left: 34px;
    top: 160px;
    display: flex;
    align-items: center;
    gap: 10px;
  }
  .brand__square {
    width: 34px; height: 34px;
    background: var(--blue);
    border-radius: 5px;
  }
  .brand__name {
    font-family: "Montserrat", sans-serif;
    font-weight: 700;
    font-size: 28px;
    color: var(--navy);
  }
  .divider {
    position: absolute;
    left: 250px;
    top: 108px;
    width: 1px;
    height: 150px;
    background: var(--divider);
  }
  .contact {
    position: absolute;
    left: 268px;
    top: 112px;
    font-size: 13px;
    line-height: 1.35;
    color: var(--ink);
  }
  .contact address { font-style: normal; margin-bottom: 10px; }
  .contact dl { display: grid; grid-template-columns: 22px auto; row-gap: 4px; }
  .contact dt { color: var(--blue); }

  /* Brand side */
  .logo-lockup {
    position: absolute;
    left: 60px;
    top: 98px;
    display: flex;
    align-items: center;
    gap: 16px;
  }
  .logo-lockup .brand__square { width: 62px; height: 62px; border-radius: 8px; }
  .logo-lockup .brand__name { font-size: 64px; letter-spacing: 1px; }
  .web {
    position: absolute;
    left: 190px;
    top: 232px;
    font-size: 15px;
    letter-spacing: 5px;
    color: var(--ink);
  }
  .web strong { color: var(--blue); font-family: "Montserrat", sans-serif; }
</style>
</head>
<body>
  <section class="card card--contact">
    <div class="rule rule--top"></div>
    <div class="name-band"><span class="person">Your Name,</span><span class="title">Title</span></div>
    <div class="rule rule--bottom"></div>
    <div class="brand">
      <span class="brand__square"></span>
      <span class="brand__name">VANTRO</span>
    </div>
    <div class="divider"></div>
    <div class="contact">
      <address>Door No. Street Name<br>City Name, State, Zip Code</address>
      <dl>
        <dt>P:</dt><dd>123-456-7890</dd>
        <dt>C:</dt><dd>123-456-7890</dd>
        <dt>E:</dt><dd>yourname@vantro.com</dd>
        <dt>W:</dt><dd>www.vantro.com</dd>
      </dl>
    </div>
  </section>

  <section class="card card--brand">
    <div class="logo-lockup">
      <span class="brand__square"></span>
      <span class="brand__name">VANTRO</span>
    </div>
    <p class="web">www.<strong>vantro</strong>.com</p>
  </section>
</body>
</html>
```